Wordpress - For IT, Cloud/Hosting, Residential/Commercial Construction Services

We are a holding company for service companies. We want the current Wordpress site modified or a new wordpress site completed. We want this site to be the parent website, that then has pull down menus linking to our other website (currently http://brightwallfix.com, http://q7v.host and would like it to be easy and fluid as we acquire more companies as we have with TKLS, Inc., B&J Construction, Brightwall Fix etc. Model after sites like Pemrose.com, Tallowbine.com, QDV.com,.vanterelm.com

------

The parent is the main site q7v Corp. Below that are sub corps and DBAs. q7v Corp stands for Quick 7 Venture Corp. q7v Offers IT manages services, 24x7 support, Monitoring NOC, Remote Hands, Onsite support services. We have acquired TKLS, Inc, B & J Construction, BrightwallFix.com. We plan to acquire/spin up many companies that offer service, support and installation offerings and will all be known as an q7v Corp Company for branding purposes. We recently had our logo done, but then ran it through 3d glass as we like the look better than the original works. We have original files in vector, but not the 3D galss door render.

Target Market(s)

IT Server and Desktop Support. Construction. Mold Remediation. Mergers and Acquisitions.

Industry/Entity Type

It Company

Coding

Coded - Design and coding required

Font styles to use
Sans Serif

Colors
0792cd

Requirements
Must have
• Clean interface. Modern design. Mobile device and multi browser support. Must be for Wordpress. Job posting with resume submission module.Hook to our Web hosting portal (Tormund) API into VexaLine Reseller portal, customer portal to allow payments to their account etc.. Easy to edit. Easy to add to, Press Release Section, Investor Relations etc.
Should not have
• Slow loading. Played out design. Over use of stock images. Copied from a competitor or something point to such.

```html
<!DOCTYPE html>
<html lang="en">
<head>
<meta charset="utf-8">
<title>q7v Corp</title>
<link href="https://fonts.googleapis.com/css2?family=Lato:wght@400;700;900&family=Open+Sans:wght@400;600&display=swap" rel="stylesheet">
<style>
:root{
  --brand:#0792cd;
  --brand-dark:#0a6aa6;
  --ink:#111;
  --text:#555;
  --muted:#888;
  --light:#f4f6f8;
  --footer:#eef0f3;
  --line:#d6dadf;
  --white:#fff;
}
*{box-sizing:border-box;margin:0;padding:0}
html,body{width:1200px;height:3593px;overflow:hidden}
body{font-family:"Open Sans",Arial,sans-serif;color:var(--text);background:var(--white);position:relative}
.abs{position:absolute}
h1,h2,h3,h4,.nav a,.btn,.label{font-family:"Lato",Arial,sans-serif}

/* hero */
.hero{left:0;top:0;width:1200px;height:630px;background:linear-gradient(120deg,#8b8273 0%,#b7ab95 35%,#a5b4c4 60%,#6e7f90 100%)}
.hero-shade{left:0;top:0;width:1200px;height:568px;background:linear-gradient(90deg,rgba(0,0,0,.35),rgba(0,0,0,.05) 60%)}
.logo{left:110px;top:30px;color:var(--white);font:900 46px/1 "Lato",sans-serif;letter-spacing:1px}
.logo small{display:block;font-size:17px;letter-spacing:8px;font-weight:700;margin-top:4px}
.nav{left:530px;top:55px;display:flex;gap:32px;align-items:center}
.nav a{color:var(--white);font-size:17px;font-weight:700;text-decoration:none}
.hero-title{left:110px;top:250px;color:var(--white);font-size:58px;line-height:1;font-weight:900;letter-spacing:1px;white-space:nowrap}
.hero-tagline{left:110px;top:326px;color:var(--white);font:700 23px/1.2 "Lato",sans-serif;white-space:nowrap}
.btn{display:inline-flex;align-items:center;gap:8px;font-weight:700;text-decoration:none}
.btn-hero{left:110px;top:383px;width:198px;height:48px;background:var(--brand);color:var(--white);font-size:18px;justify-content:center}
.news{left:0;top:568px;width:1200px;height:62px;background:var(--brand)}
.news-tag{left:0;top:568px;width:320px;height:62px;background:#123049;clip-path:polygon(0 0,290px 0,320px 31px,290px 62px,0 62px)}
.news-tag span{position:absolute;left:112px;top:17px;color:var(--white);font:900 23px "Lato",sans-serif}
.news-text{left:350px;top:588px;color:var(--white);font-size:15px}

/* welcome */
.welcome{left:0;top:630px;width:1200px;height:610px;background:var(--light)}
.section-title{width:1200px;left:0;text-align:center;color:var(--ink);font-size:37px;font-weight:900}
.intro{left:220px;width:760px;top:778px;text-align:center;font-size:12.5px;line-height:29px}
.about-title{left:110px;top:880px;color:var(--ink);font-size:30px;font-weight:700;letter-spacing:1px}
.about-copy{left:110px;width:475px;font-size:12px;line-height:22px}
.btn-outline{border:2px solid var(--brand);color:var(--brand);background:var(--white);justify-content:center;font-size:14px}
.video{left:642px;top:891px;width:450px;height:299px}
.video .shot{position:absolute;left:10px;top:10px;width:430px;height:279px;background:linear-gradient(135deg,#c9d2da,#8b98a5 60%,#5d6770)}
.corner{position:absolute;width:26px;height:26px;border-color:var(--brand);border-style:solid}
.play{position:absolute;left:200px;top:125px;width:54px;height:38px;background:#e02020;border-radius:9px}
.play:after{content:"";position:absolute;left:21px;top:10px;border-left:16px solid #fff;border-top:9px solid transparent;border-bottom:9px solid transparent}

/* services */
.tile{width:578px;height:326px;overflow:hidden}
.tile .photo{position:absolute;inset:0}
.tile .veil{position:absolute;inset:0;background:linear-gradient(0deg,rgba(0,0,0,.55),rgba(0,0,0,.05) 70%)}
.tile h4{position:absolute;left:58px;color:var(--white);font-size:29px;font-weight:900;letter-spacing:1px}
.tile p{position:absolute;left:58px;width:470px;color:var(--white);font-size:12.5px;line-height:22px;font-weight:600}
.tile .more{position:absolute;left:58px;color:var(--white);font:900 15px "Lato",sans-serif}

/* why */
.why{left:0;top:1975px;width:1200px;height:450px;background:var(--light)}
.feature{width:220px;text-align:center}
.feature .circle{width:144px;height:144px;border-radius:50%;background:var(--white);margin:0 auto;display:flex;align-items:center;justify-content:center;box-shadow:0 2px 8px rgba(0,0,0,.08)}
.feature .label{margin-top:34px;color:var(--ink);font-size:22px;font-weight:700}

/* blog */
.post{width:298px}
.post .thumb{width:298px;height:211px}
.post h4{margin-top:32px;color:var(--ink);font-size:21px;font-weight:700;white-space:nowrap}
.post .meta{margin-top:12px;font-size:12px;color:var(--text);display:flex;gap:28px}
.post .meta span{display:inline-flex;gap:7px;align-items:center}
.post p{margin-top:18px;font-size:12px;line-height:21px}
.post .btn{margin-top:22px;width:138px;height:36px;font-size:13px}
.btn-solid{background:var(--brand);color:var(--white);justify-content:center}

/* footer */
.footer{left:0;top:3176px;width:1200px;height:417px;background:var(--footer)}
.footer-title{color:var(--ink);font-size:17px;font-weight:700}
.col{top:3250px}
.col ul{list-style:none;margin-top:18px}
.col li{font-size:11.5px;line-height:27px;display:flex;gap:12px;align-items:center}
.col li:before{content:"›";color:var(--brand);font-weight:700}
.contact-row{display:flex;gap:18px;font-size:11.5px;line-height:18px;margin-top:18px}
.field{width:240px;height:34px;border:1px solid var(--line);background:var(--white);font-size:11px;padding:9px 10px;color:var(--muted);margin-top:14px}
.socials{left:474px;top:3436px;display:flex;gap:13px}
.socials span{width:40px;height:40px;border:2px solid #7a8290;border-radius:50%;display:block}
.rule{left:110px;top:3500px;width:980px;height:1px;background:var(--line)}
.copyright{left:0;width:1200px;top:3540px;text-align:center;font-size:13px;color:#444}
</style>
</head>
<body>

<!-- hero -->
<div class="abs hero" role="img" aria-label="Engineer in hard hat working on a laptop at a construction site"></div>
<div class="abs hero-shade"></div>
<div class="abs logo">q7v<small>CORP</small></div>
<nav class="abs nav"><a href="#">HOME</a><a href="#">ABOUT US</a><a href="#">SERVICES</a><a href="#">COMPANY ▾</a><a href="#">CONTACT US</a>
<svg width="18" height="18" viewBox="0 0 18 18"><circle cx="7.5" cy="7.5" r="5.5" fill="none" stroke="#fff" stroke-width="2.4"/><line x1="11.5" y1="11.5" x2="16.5" y2="16.5" stroke="#fff" stroke-width="2.6"/></svg></nav>
<h1 class="abs hero-title">QUICK 7 VENTURE</h1>
<div class="abs hero-tagline">q7v is a Corvane and Tallowbine IT Solution Partner</div>
<a class="abs btn btn-hero" href="#">CONTACT US
<svg width="16" height="16" viewBox="0 0 16 16"><circle cx="8" cy="8" r="8" fill="#fff"/><path d="M6 4l4 4-4 4" stroke="#0792cd" stroke-width="2" fill="none"/></svg></a>
<div class="abs news"></div>
<div class="abs news-tag"><span>LATEST NEWS</span></div>
<div class="abs news-text">Lorem ipsum dolor sit amet consectetur adipiscing sed do eiusmod tempor incididunt ut labore.</div>

<!-- welcome -->
<section class="abs welcome"></section>
<h2 class="abs section-title" style="top:712px">WELCOME TO q7v CORP</h2>
<p class="abs intro">Lorem ipsum dolor sit amet, consectetur adipiscing elit, sed do eiusmod tempor incididunt ut labore et dolore magna aliqua. Ut enim ad minim veniam, quis nostrud exercitation ullamco laboris nisi ut aliquip ex ea commodo consequat.</p>
<h3 class="abs about-title">A LITTLE ABOUT q7v CORP</h3>
<p class="abs about-copy" style="top:950px">Nemo enim ipsam voluptatem quia voluptas sit aspernatur aut odit aut fugit, sed quia consequuntur magni dolores eos qui ratione.</p>
<p class="abs about-copy" style="top:1015px">Voluptatem sequi nesciunt. Neque porro quisquam est, qui dolorem ipsum quia dolor sit amet, consectetur, adipisci velit, sed quia non numquam eius modi tempora incidunt ut labore et dolore magnam aliquam quaerat voluptatem. Ut enim ad minima veniam, quis nostrum exercitationem ullam corporis.</p>
<a class="abs btn btn-outline" href="#" style="left:110px;top:1150px;width:157px;height:42px">READ MORE
<svg width="14" height="14" viewBox="0 0 16 16"><circle cx="8" cy="8" r="8" fill="#0792cd"/><path d="M6 4l4 4-4 4" stroke="#fff" stroke-width="2" fill="none"/></svg></a>
<div class="abs video">
  <div class="shot" role="img" aria-label="Video still of colleagues working together in an office"></div>
  <span class="corner" style="left:0;top:0;border-width:4px 0 0 4px"></span>
  <span class="corner" style="right:0;top:0;border-width:4px 4px 0 0"></span>
  <span class="corner" style="left:0;bottom:0;border-width:0 0 4px 4px"></span>
  <span class="corner" style="right:0;bottom:0;border-width:0 4px 4px 0"></span>
  <span class="play"></span>
</div>

<!-- services -->
<div class="abs tile" style="left:14px;top:1286px">
  <div class="photo" role="img" aria-label="IT staff working at computers in an office" style="background:linear-gradient(135deg,#5a6470,#2e3640 55%,#1c2228)"></div><div class="veil"></div>
  <h4 style="top:172px">IT SERVICES</h4>
  <p style="top:220px">Lorem ipsum dolor sit amet, consectetur adipiscing elit, sed do eiusmod tempor incididunt ut labore et dolore magna aliqua.</p>
</div>
<div class="abs tile" style="left:608px;top:1286px">
  <div class="photo" role="img" aria-label="Blue-lit server room aisle" style="background:linear-gradient(135deg,#1b6fb8,#0a4f93 50%,#0d3f7a)"></div><div class="veil" style="background:rgba(7,110,190,.25)"></div>
  <h4 style="top:142px">CLOUD/HOSTING</h4>
  <p style="top:190px">Lorem ipsum dolor sit amet, consectetur adipiscing elit, sed do eiusmod tempor incididunt ut labore et dolore magna aliqua.</p>
  <span class="more" style="top:258px">READ MORE ⊕</span>
</div>
<div class="abs tile" style="left:14px;top:1631px">
  <div class="photo" role="img" aria-label="Modern glass office buildings beside a tree-lined path" style="background:linear-gradient(160deg,#7fa3c6,#5d7890 45%,#3f5a3a 85%)"></div><div class="veil"></div>
  <h4 style="top:172px">COMMERCIAL</h4>
  <p style="top:220px">Lorem ipsum dolor sit amet, consectetur adipiscing elit, sed do eiusmod tempor incididunt ut labore et dolore magna aliqua.</p>
</div>
<div class="abs tile" style="left:608px;top:1631px">
  <div class="photo" role="img" aria-label="Building under construction with cranes and scaffolding" style="background:linear-gradient(160deg,#3d7fc4,#6a8fb3 40%,#8a7a60 80%)"></div><div class="veil"></div>
  <h4 style="top:172px">CONSTRUCTION</h4>
  <p style="top:220px">Lorem ipsum dolor sit amet, consectetur adipiscing elit, sed do eiusmod tempor incididunt ut labore et dolore magna aliqua.</p>
</div>

<!-- why choose us -->
<section class="abs why"></section>
<h2 class="abs section-title" style="top:2055px">WHY CHOOSE US?</h2>
<div class="abs feature" style="left:82px;top:2143px"><div class="circle">
<svg width="78" height="78" viewBox="0 0 78 78" fill="none" stroke="#0792cd" stroke-width="3"><path d="M14 40a25 25 0 0 1 50 0"/><rect x="8" y="38" width="10" height="18" rx="3"/><rect x="60" y="38" width="10" height="18" rx="3"/><path d="M65 56c0 10-10 14-20 14"/><text x="39" y="50" text-anchor="middle" font-family="Lato" font-size="15" font-weight="900" fill="#0792cd" stroke="none">24/7</text></svg>
</div><div class="label">24X7 SUPPORT</div></div>
<div class="abs feature" style="left:347px;top:2143px"><div class="circle">
<svg width="78" height="78" viewBox="0 0 78 78" fill="none" stroke="#0792cd" stroke-width="3"><rect x="8" y="12" width="62" height="42" rx="3"/><path d="M30 66h18M39 54v12"/><circle cx="22" cy="28" r="3"/><circle cx="34" cy="40" r="3"/><path d="M24 30l8 8M36 38l10-10"/><path d="M48 22h14M48 30h14M48 38h10"/></svg>
</div><div class="label">MONITORING NOC</div></div>
<div class="abs feature" style="left:616px;top:2143px"><div class="circle">
<svg width="78" height="78" viewBox="0 0 78 78" fill="none" stroke="#0792cd" stroke-width="3"><path d="M14 64l30-30M20 70l-10-10 6-6 10 10z"/><path d="M48 12a14 14 0 0 0-12 18L12 54"/><path d="M40 44l24 24 6-6-24-24"/><path d="M56 22a10 10 0 0 1 10 10l-8-2-2-8z"/></svg>
</div><div class="label">REMOTE HANDS</div></div>
<div class="abs feature" style="left:881px;top:2143px"><div class="circle">
<svg width="78" height="78" viewBox="0 0 78 78" fill="none" stroke="#0792cd" stroke-width="3"><rect x="18" y="10" width="42" height="34" rx="3"/><circle cx="39" cy="24" r="6"/><path d="M28 38c3-6 19-6 22 0"/><rect x="12" y="48" width="54" height="20" rx="2"/><path d="M20 56h22M20 62h14"/></svg>
</div><div class="label">ONSITE SUPPORT</div></div>

<!-- blog -->
<h2 class="abs section-title" style="top:2517px">LATEST BLOG POST</h2>
<article class="abs post" style="left:112px;top:2603px">
  <div class="thumb" role="img" aria-label="Technician with a laptop in a server room" style="background:linear-gradient(135deg,#2a3d6a,#5b6c8c 55%,#c7c9cf)"></div>
  <h4>Lorem ipsum dolor consectetur</h4>
  <div class="meta"><span>▦ Sep 13, 2018</span><span>● Jhon Deo</span></div>
  <p>Lorem ipsum dolor sit amet, consectetur adipiscing elit, sed do eiusmod tempor incididunt ut labore et dolore magna aliquaminim veniam quis...</p>
  <a class="btn btn-outline" href="#" style="border-width:1px;border-color:#bbb">READ MORE ⊕</a>
</article>
<article class="abs post" style="left:450px;top:2603px">
  <div class="thumb" role="img" aria-label="Office corridor with a cleaning cart" style="background:linear-gradient(180deg,#e6e4df,#c9c3b6 60%,#a89f8c)"></div>
  <h4>Nemo enim ipsam voluptatem</h4>
  <div class="meta"><span>▦ Sep 13, 2018</span><span>● Jhon Deo</span></div>
  <p>Lorem ipsum dolor sit amet, consectetur adipiscing elit, sed do eiusmod tempor incididunt ut labore et dolore magna aliquaminim veniam quis...</p>
  <a class="btn btn-solid" href="#">READ MORE ⊕</a>
</article>
<article class="abs post" style="left:793px;top:2603px">
  <div class="thumb" role="img" aria-label="Person reviewing charts on a laptop by a city window" style="background:linear-gradient(135deg,#2b2f36,#707a86 55%,#d7dbe0)"></div>
  <h4>Nor again is there anyone who</h4>
  <div class="meta"><span>▦ Sep 13, 2018</span><span>● Jhon Deo</span></div>
  <p>Lorem ipsum dolor sit amet, consectetur adipiscing elit, sed do eiusmod tempor incididunt ut labore et dolore magna aliquaminim veniam quis...</p>
  <a class="btn btn-outline" href="#" style="border-width:1px;border-color:#bbb">READ MORE ⊕</a>
</article>

<!-- footer -->
<footer class="abs footer"></footer>
<div class="abs col" style="left:110px;width:280px"><h4 class="footer-title">CONTACT US</h4>
  <div class="contact-row" style="margin-top:24px"><svg width="12" height="16" viewBox="0 0 12 16"><path d="M6 0a6 6 0 0 1 6 6c0 4-6 10-6 10S0 10 0 6a6 6 0 0 1 6-6z" fill="#0792cd"/><circle cx="6" cy="6" r="2" fill="#fff"/></svg><span>q7v Corp<br>123 Sample Str, New State CA 93721.</span></div>
  <div class="contact-row" style="margin-top:20px"><svg width="14" height="14" viewBox="0 0 14 14"><path d="M3 0l3 3-2 2c1 2 3 4 5 5l2-2 3 3-2 3C6 14 0 8 0 3z" fill="#0792cd"/></svg><span>(+123) 456 7890</span></div>
  <div class="contact-row" style="margin-top:20px"><svg width="15" height="11" viewBox="0 0 15 11"><rect width="15" height="11" fill="#0792cd"/><path d="M0 0l7.5 6L15 0" stroke="#fff" fill="none"/></svg><span>info@quick7venturecorp.com</span></div>
</div>
<div class="abs col" style="left:421px"><h4 class="footer-title">QUICK LINKS</h4><ul><li>Home</li><li>About Us</li><li>Our Services</li><li>Company</li><li>Contact Us</li></ul></div>
<div class="abs col" style="left:620px"><h4 class="footer-title">SUPPORT</h4><ul><li>Meet Our Team</li><li>Onsite Support</li><li>Investors</li><li>News &amp; Blog</li><li>Terms Of Services</li></ul></div>
<div class="abs col" style="left:845px;width:250px"><h4 class="footer-title">NEWSLETTER SUBSCRIPTION</h4>
  <p style="font-size:11px;line-height:18px;margin-top:22px">Register your Email Address to get more information about us</p>
  <div class="field">Email Address</div>
  <a class="btn btn-solid" href="#" style="margin-top:12px;width:112px;height:34px;font-size:12px">SUBSCRIBE</a>
</div>
<div class="abs socials"><span></span><span></span><span></span><span></span><span></span></div>
<div class="abs rule"></div>
<div class="abs copyright">Copyrights © 2018 q7v Corp. All Rights Reserved &nbsp; | &nbsp; Privacy Policy.</div>

</body>
</html>
```